Vessel Pour Meridian wine is looking for a modern, bold contemporary abstract logo/brand design

We are wholesale distributor based in Napa Valley / Sonoma county in California, USA which needs an universal logo/brand name design for all our potential products include pouches, tetra pak and Bag in Box package. All products will be export to Asia predominantly in the greater China market we have yet finalize on company name at this moment but leaning toward "Talvin" as our brand name.

With our target group age between 21-45, we would like to see modern designs that is suitable for our target audience which include minimum requirement usage in colors of Red and Gold to reflect the Asian culture with generic grape, vineyard and other wine industry images. As an alternate option, image can also be formed in any musical instrument or even in animal symbols such as cheetah and black panther whatever suitable to the overall design. We want the image of the product to be stand out from other competitor envision the box design as royal, luxury with texture in modern twist.

The final design should communicate environmental safety, wine composition information (bottle wine equivalent volume images, place of origin such as Made in the U.S.A., Napa Valley, Sonoma, California wordings and all other wine industry standard relevant information listed on package).

Attached pictures are for your reference.

Target Market(s)

Age group 21-45, Asia market predominately in the greater China region

Industry/Entity Type

Distributor

Font styles to use
Serif
Decorative
Script

Requirements
Must have
• 1. Modern bold contemporary abstract design - see attached
• 2. Prefer colors in mixture of Gold, Red, Black in Red Wine package, and colors in mixture of Gold, Silver, Copper, Brass, Steel in White Wine package.
• 3. Brand name "Talvin"
Nice to have
• 1. Generic grapes, vineyard, wine industry images and/or non-winery images in musical instrument or animal symbol such as horse in standing figure whatever suitable to the overall design concept.
• 2. Place of origin wordings such as Products of U.S.A., California Red Wine and etc.

```html
<!DOCTYPE html>
<html lang="en">
<head>
<meta charset="UTF-8">
<title>Talvin – California Premium Red</title>
<link rel="stylesheet" href="https://fonts.googleapis.com/css2?family=Orbitron:wght@900&family=Lato:wght@400&display=swap">
<style>
  :root {
    --ink: #000000;
    --ember: #ff7a12;
    --ember-deep: #b84a08;
    --ember-mid: #e8650c;
    --glow-strong: rgba(255, 118, 20, 0.55);
    --glow-soft: rgba(230, 90, 10, 0.28);
  }
  * { margin: 0; padding: 0; box-sizing: border-box; }
  html, body {
    width: 1200px;
    height: 2745px;
    overflow: hidden;
    background: var(--ink);
  }
  .package-face {
    position: relative;
    width: 1200px;
    height: 2745px;
    background: var(--ink);
  }
  .storm-art {
    position: absolute;
    left: 0;
    width: 1200px;
  }
  .storm-art--top {
    top: 0;
    height: 1330px;
    background:
      radial-gradient(ellipse 160px 520px at 33% 45%, var(--glow-strong), transparent 75%),
      radial-gradient(ellipse 420px 120px at 80% 12%, var(--glow-strong), transparent 75%),
      radial-gradient(ellipse 360px 110px at 82% 60%, var(--glow-strong), transparent 75%),
      radial-gradient(ellipse 140px 420px at 62% 80%, var(--glow-strong), transparent 75%),
      radial-gradient(ellipse 200px 260px at 10% 88%, var(--glow-soft), transparent 75%),
      radial-gradient(ellipse 260px 180px at 22% 10%, var(--glow-soft), transparent 75%),
      radial-gradient(ellipse 700px 900px at 50% 50%, rgba(120, 40, 0, 0.25), transparent 80%),
      var(--ink);
  }
  .storm-art--bottom {
    top: 1961px;
    height: 784px;
    background:
      radial-gradient(ellipse 380px 130px at 22% 18%, var(--glow-strong), transparent 75%),
      radial-gradient(ellipse 180px 360px at 32% 60%, var(--glow-soft), transparent 75%),
      radial-gradient(ellipse 440px 160px at 78% 48%, var(--glow-strong), transparent 75%),
      radial-gradient(ellipse 150px 380px at 90% 30%, var(--glow-soft), transparent 75%),
      radial-gradient(ellipse 300px 140px at 62% 88%, var(--glow-soft), transparent 75%),
      radial-gradient(ellipse 700px 600px at 55% 50%, rgba(120, 40, 0, 0.25), transparent 80%),
      var(--ink);
  }
  .divider-rule {
    position: absolute;
    left: 0;
    width: 1200px;
    height: 10px;
    background: linear-gradient(90deg, var(--ember-deep), var(--ember-mid) 50%, var(--ember));
  }
  .divider-rule--upper { top: 1330px; }
  .divider-rule--lower { top: 1950px; height: 11px; }
  .brand-lockup {
    position: absolute;
    left: 0;
    top: 1470px;
    width: 1200px;
    display: flex;
    justify-content: center;
    align-items: center;
    gap: 28px;
  }
  .brand-lockup__dot {
    width: 54px;
    height: 54px;
    border-radius: 50%;
    background: var(--ember-mid);
  }
  .brand-lockup__name {
    font-family: "Lato", sans-serif;
    font-weight: 400;
    font-size: 104px;
    line-height: 1;
    color: var(--ember-mid);
  }
  .brand-name {
    position: absolute;
    left: 0;
    top: 1718px;
    width: 1200px;
    text-align: center;
    font-family: "Orbitron", sans-serif;
    font-weight: 900;
    font-size: 50px;
    letter-spacing: 0.6em;
    text-indent: 0.6em;
    color: var(--ember-mid);
    line-height: 1;
  }
  .wine-style {
    position: absolute;
    left: 0;
    top: 1872px;
    width: 1200px;
    text-align: center;
    font-family: "Lato", sans-serif;
    font-weight: 400;
    font-size: 33px;
    letter-spacing: 0.45em;
    text-indent: 0.45em;
    color: var(--ember);
    line-height: 1;
  }
</style>
</head>
<body>
  <main class="package-face">
    <div class="storm-art storm-art--top" role="img" aria-label="Glowing orange lightning bolts branching across a black sky"></div>
    <div class="divider-rule divider-rule--upper"></div>

    <div class="brand-lockup">
      <span class="brand-lockup__dot" aria-hidden="true"></span>
      <span class="brand-lockup__name">Talvin</span>
    </div>
    <h1 class="brand-name">TALVIN</h1>
    <p class="wine-style">California Premium Red</p>

    <div class="divider-rule divider-rule--lower"></div>
    <div class="storm-art storm-art--bottom" role="img" aria-label="Glowing orange lightning bolts branching across a black sky"></div>
  </main>
</body>
</html>
```